TK Homes - Stone Dorf Design

Looking for a double sides design, 1 side for my realestate and the other for home building. ( TK Homes on 1 side, Stone Dorf card on the other Side
Side 1 - Marek Tove ~ Vox Realty logo and Company ( the Property quarter )
Marek Tove
Marek@Marektove.example
IG - Marek_Bzq_Realtor
FB - marekt
Cell - 5558130467
3847 61 St Nw

Side 2
Marek Tove
5558130467
IG - Stonedorf_Bzq
Stonedorfdev@mailbox.example

Target Market(s)

Home buyers/ sellers

Industry/Entity Type

Home builders - Realestate

Contact Information for Business Card

Above

Requirements
Must have
• Black OR White background - my information -

```html
<!DOCTYPE html>
<html lang="en">
<head>
<meta charset="utf-8">
<title>Stone Dorf Developments and Marek Tove business cards</title>
<link rel="stylesheet" href="https://fonts.googleapis.com/css2?family=Tinos:wght@400;700&display=swap">
<style>
  :root {
    --stage: #3a3b40;
    --card: #1e1e22;
    --blue: #1474c4;
    --red: #e0503f;
    --white: #f4f4f4;
    --rule: #cfcfcf;
  }
  html, body {
    margin: 0;
    padding: 0;
    width: 1200px;
    height: 780px;
    overflow: hidden;
    background: var(--stage);
    font-family: "Tinos", "Times New Roman", serif;
  }
  .canvas {
    position: relative;
    width: 1200px;
    height: 780px;
  }
  .card {
    position: absolute;
    left: 300px;
    width: 600px;
    height: 343px;
    background: var(--card);
    box-shadow: 0 10px 28px rgba(0,0,0,.45);
    overflow: hidden;
  }
  .card--builder { top: 26px; }
  .card--realtor { top: 411px; }

  .brand {
    position: absolute;
    display: flex;
    align-items: center;
    gap: 12px;
    color: var(--blue);
    font-weight: 700;
  }
  .brand__mark {
    width: 18px;
    height: 18px;
    background: var(--red);
    flex: none;
  }
  .card--builder .brand { left: 48px; top: 70px; font-size: 30px; line-height: 1.05; }
  .card--realtor .brand { left: 110px; top: 62px; font-size: 42px; letter-spacing: 1px; }

  .person {
    position: absolute;
    left: 70px;
    top: 196px;
    font-weight: 700;
  }
  .person__name { font-size: 36px; line-height: 1; }
  .person__first { color: var(--blue); }
  .person__last { color: var(--red); }
  .person__title {
    color: var(--white);
    font-size: 17px;
    margin: 4px 0 0 110px;
  }

  .divider {
    position: absolute;
    left: 318px;
    top: 165px;
    width: 1px;
    height: 92px;
    background: var(--rule);
  }
  .card--realtor .divider { top: 150px; height: 110px; }

  .contacts {
    position: absolute;
    left: 338px;
    margin: 0;
    padding: 0;
    list-style: none;
    color: var(--white);
    font-size: 15.5px;
    line-height: 1.45;
  }
  .card--builder .contacts { top: 160px; }
  .card--realtor .contacts { top: 142px; }
  .contacts li { display: flex; align-items: center; gap: 9px; white-space: nowrap; }
  .icon { width: 14px; height: 14px; flex: none; }
  .icon--dot { width: 12px; height: 12px; border-radius: 50%; background: var(--blue); margin: 0 1px; }
  .icon--box { width: 11px; height: 11px; border: 1.5px solid var(--blue); border-radius: 3px; margin: 0 1px; }

  .band {
    position: absolute;
    left: 0;
    right: 0;
    top: 282px;
    height: 28px;
    background: var(--red);
    color: var(--white);
    font-size: 15px;
    line-height: 28px;
    padding-left: 318px;
    box-sizing: border-box;
  }
</style>
</head>
<body>
<main class="canvas">

  <section class="card card--builder" aria-label="Stone Dorf Developments card">
    <div class="brand"><span class="brand__mark"></span><span>Stone Dorf<br>Developments</span></div>
    <div class="person">
      <div class="person__name"><span class="person__first">Marek</span> <span class="person__last">Tove</span></div>
      <div class="person__title">Director</div>
    </div>
    <div class="divider"></div>
    <ul class="contacts">
      <li><svg class="icon" viewBox="0 0 14 14"><path d="M3 1l2.5 2.5-1.3 1.6a8 8 0 0 0 4.7 4.7l1.6-1.3L13 11l-1.6 2C6 13 1 8 1 2.6z" fill="var(--blue)"/></svg>5558130467</li>
      <li><span class="icon icon--box"></span>Stonedorf_Bzq</li>
      <li><svg class="icon" viewBox="0 0 14 14"><rect x="1" y="3" width="12" height="8" fill="var(--blue)"/><path d="M1 3l6 5 6-5" fill="none" stroke="var(--card)" stroke-width="1.2"/></svg>Stonedorfdev@mailbox.example</li>
    </ul>
    <div class="band">3847 61 St Nw</div>
  </section>

  <section class="card card--realtor" aria-label="Marek Tove realtor card">
    <div class="brand"><span class="brand__mark"></span><span>Marek Tove</span></div>
    <div class="person">
      <div class="person__name"><span class="person__first">Marek</span> <span class="person__last">Tove</span></div>
      <div class="person__title">Director</div>
    </div>
    <div class="divider"></div>
    <ul class="contacts">
      <li><svg class="icon" viewBox="0 0 14 14"><path d="M3 1l2.5 2.5-1.3 1.6a8 8 0 0 0 4.7 4.7l1.6-1.3L13 11l-1.6 2C6 13 1 8 1 2.6z" fill="var(--blue)"/></svg>5558130467</li>
      <li><span class="icon icon--dot"></span>marekt</li>
      <li><span class="icon icon--box"></span>Marek_Bzq_Realtor</li>
      <li><svg class="icon" viewBox="0 0 14 14"><rect x="1" y="3" width="12" height="8" fill="var(--blue)"/><path d="M1 3l6 5 6-5" fill="none" stroke="var(--card)" stroke-width="1.2"/></svg>Marek@Marektove.example</li>
      <li><svg class="icon" viewBox="0 0 14 14"><g fill="none" stroke="var(--blue)" stroke-width="1.2"><circle cx="7" cy="7" r="6"/><ellipse cx="7" cy="7" rx="2.6" ry="6"/><path d="M1 7h12M2 4h10M2 10h10"/></g></svg>www.marektove.example</li>
    </ul>
    <div class="band">3847 61 St Nw</div>
  </section>

</main>
</body>
</html>
```